Lotstallmart.com Webpage Design

Design Brief for lotstallmart.com (Copy of Brief also in attached Word file)

Name of Website- lotstallmart.com (existing logo and look & feel of website to be changed)

Logo - Finalised. The logo files are attached with the brief as “logo.jpeg”. The “Blue- Grey” version of the logo is for use on lighter backgrounds and the “Orange-White” version of the logo is for use on darker backgrounds. (A full Black version of the logo is also attached). Both versions may be used in different parts of the website. All attached files are in .png format.
Status - The website in functional and is undergoing user trials. However, we want to improve the look & feel of the website so at it seems
a. cotemporary,
b. Easy to Navigate
c. professional and
d. Vibrant.

Please visit ‘lotstallmart.com’ to check out the website and its functionalities – please use it only as a reference for the features & functions to be provided, however the designer should use a ‘Free Hand’ in designing the composition of various parts of the webpage without getting too influenced by the existing design

Objective of the Website ‘lotstallmart.com –
a. It is a portal focussed on listing of ‘Retail’ specific real-estate properties by developers, owners and realty brokers. The properties shall listed under the following four categories-
i. Retail Malls
ii. Shopping Complexes
iii. High-street shops
iv. Retail Warehouses
*refer lotstallmart.com for better clarity

b. The abovementioned properties shall be listed either for ‘Sale’ or ‘rent\lease’ or both

c. Users shall visit the site in case they wish to acquire a retail \ shop space either on ‘sale’ or ‘rent’. These Users would be able to specify the ‘Search Criteria’ through the tool-bars provided on the website – the ‘Search Criteria’ shall comprise of ‘Type of space category’, ‘City’, ‘Locality’, transaction type ie ‘Rent \ Sale’ and ‘Area Range’

d. The main revenue model for the website shall be listing fee ( or advertising charges ) payable by those listing their properties on the website.

Three Main Pages of Website (lotstallmart.com) that need to be designed -
a. Main Home Page (visit the web link - http://lotstallmart.com/ ) - The main home page has the “Search Toolbar” for specifying of Search Criteria by the User. It shall also have the following features & functions-
i. Main Advertising Banner
ii. Featured Projects
iii. New Launches
iv. Toolbar with buttons – ‘Advertise with Us’, ‘Listings Alert’, ‘Mart Wizards’, ‘Advertiser Login’

b. Property Listings Page (visit the web link - http://lotstallmart.com/gurgaon-in-india ) - The List of property options that match the Criteria specified by the ‘User’ get displayed on this page.

c. Property Detail Page - When the ‘User’ clicks on the “More….” Button on the ‘Property Listings Page’ (given in point b. above) the web page with the details of the property opens. (For Example – visit the web link - http://lotstallmart.com/vorne-Shopping-Complex-vorne-quadrion-gurgaon-636 )

Note:- Please refer to attached ‘Shopping’ related images the designer may use them on the website to provide a look & feel of retail if required – either separately or rotate in a single window

Target Market(s)

Retailers & Investors looking for retail space, Real Estate Brokers, Developers

Industry/Entity Type

Advertising

Number of Pages Required

3 page

Requirements
Must have
• Refer to existing site lotstallmart.com -- all the existing functionalities are a must have.
Nice to have
• The Designer may use the retail related images on the website if required for making it more vibrant. Refer attached images Shopping(1-6).jpg

```html
<!DOCTYPE html>
<html lang="en">
<head>
<meta charset="utf-8">
<title>lotstallmart.com – Retail Space Portal</title>
<link href="https://fonts.googleapis.com/css2?family=Open+Sans:wght@400;600;700&display=swap" rel="stylesheet">
<style>
:root{
  --topbar:#3b3b3d;
  --page:#e9e9ea;
  --white:#ffffff;
  --blue:#1a73b8;
  --blue-dark:#0f5a9a;
  --blue-deep:#0b4f8a;
  --blue-field:#0e5d9e;
  --tile1:#115e9e;
  --tile2:#1469ad;
  --tile3:#1a76bd;
  --tile4:#1f82c9;
  --tile-text:#7ed3ff;
  --orange:#f0851a;
  --orange-deep:#e27410;
  --title-orange:#d9640f;
  --text:#333335;
  --muted:#7a7a7c;
  --btn:#efefef;
  --btn-border:#d8d8d8;
  --side-grey:#f1f1f2;
  --footer:#4a4a4e;
  --footer-bottom:#3f3f43;
  --footer-text:#d8d8da;
}
*{box-sizing:border-box;margin:0;padding:0}
html,body{width:1200px;height:2335px;overflow:hidden}
body{background:var(--page);font-family:"Open Sans",Arial,sans-serif;color:var(--text);position:relative}

/* top city bar */
.city-bar{height:37px;background:var(--topbar);display:flex;justify-content:center}
.city-bar a{color:#d5d5d7;font-size:12px;text-decoration:none;line-height:37px;padding:0 20px;border-right:1px solid #555}
.city-bar a:last-child{border-right:none}

/* header */
.site-header{height:84px;background:var(--white);position:relative;box-shadow:0 1px 2px rgba(0,0,0,.08)}
.brand{position:absolute;left:100px;top:16px;display:flex;align-items:center;gap:8px}
.brand-dot{width:30px;height:30px;border-radius:50%;background:var(--blue)}
.brand-name{font-size:28px;font-weight:700;color:var(--blue);line-height:1}
.brand-tag{position:absolute;left:138px;top:52px;font-size:7px;font-weight:700;color:var(--blue-dark);letter-spacing:.3px}
.header-nav{position:absolute;left:411px;top:26px;display:flex}
.header-nav .item{width:180px}
.header-nav .label{font-size:11px;font-weight:600;color:#444;text-transform:uppercase}
.header-nav .sub{font-size:11px;color:#999;margin-top:5px}
.login-btns{position:absolute;left:927px;top:0;width:173px}
.login-btns a{display:block;height:42px;line-height:42px;text-align:center;color:#fff;font-size:12px;font-weight:700;text-decoration:none;text-transform:uppercase}
.login-btns .advertiser{background:var(--blue)}
.login-btns .register{background:var(--orange)}

/* hero */
.hero{position:absolute;left:100px;top:121px;width:1000px;height:436px;display:flex}
.search-panel{width:315px;flex-shrink:0;height:436px;background:var(--blue);padding:32px 24px 0}
.search-panel h2{color:#fff;font-size:20px;font-weight:700;text-align:center;line-height:1.2}
.search-panel .sub-title{color:#fff;font-size:18px;text-align:center;margin-top:2px;text-transform:uppercase}
.format-box{background:var(--blue-field);margin-top:18px;padding:14px 14px 10px;display:grid;grid-template-columns:1fr 1fr;row-gap:12px;border:1px solid #1b6bab}
.format-box label{color:#fff;font-size:11px;display:flex;align-items:center;gap:6px}
.format-box span.check{width:12px;height:12px;background:#3a8fd3;border:1px solid #6cb1e6}
.field{margin-top:16px;height:30px;background:var(--blue-field);color:#fff;font-size:11px;line-height:30px;padding:0 14px;position:relative}
.format-box + .field{margin-top:22px}
.field::after{content:"";position:absolute;right:12px;top:13px;border:4px solid transparent;border-top-color:#fff}
.search-btn{display:block;margin:20px 0 0 145px;width:122px;height:38px;background:var(--orange);color:#fff;font-size:13px;line-height:38px;text-align:center;border-radius:2px}
.search-btn svg{vertical-align:-2px;margin-right:6px}
.hero-photo{width:685px;height:436px;position:relative;background:
  radial-gradient(ellipse 22% 30% at 30% 10%,rgba(255,214,150,.55),transparent 70%),
  radial-gradient(ellipse 18% 25% at 82% 18%,rgba(255,226,170,.45),transparent 70%),
  radial-gradient(ellipse 30% 45% at 70% 70%,rgba(196,90,150,.35),transparent 70%),
  radial-gradient(ellipse 25% 40% at 45% 65%,rgba(70,95,140,.45),transparent 70%),
  linear-gradient(180deg,#4a3726 0%,#6a5238 40%,#3a2c22 75%,#241c17 100%)}
.hero-arrows{position:absolute;right:8px;bottom:88px;display:flex;gap:2px}
.hero-arrows span{width:20px;height:20px;background:rgba(0,0,0,.45);color:#fff;font-size:12px;text-align:center;line-height:19px}

/* sidebar */
.sidebar{position:absolute;left:870px;top:478px;width:230px}
.cat-tile{height:81px;padding:20px 0 0 25px}
.cat-tile:nth-child(1){background:var(--tile1)}
.cat-tile:nth-child(2){background:var(--tile2)}
.cat-tile:nth-child(3){background:var(--tile3)}
.cat-tile:nth-child(4){background:var(--tile4)}
.cat-tile h3{color:var(--tile-text);font-size:13px;font-weight:700;text-transform:uppercase}
.cat-tile p{color:#fff;font-size:9px;font-weight:600;text-transform:uppercase;margin-top:5px}
.cat-tile p .ring{display:inline-block;width:10px;height:10px;border:1px solid #fff;border-radius:50%;vertical-align:-2px;margin-left:5px}
.wizards{background:var(--orange);height:377px;padding:25px 22px 0 23px}
.wizards h3,.alert h3,.about h3{font-size:13px;font-weight:700;text-transform:uppercase}
.wizards h3{color:#fff}
.wizards p{color:#fff;font-size:11px;line-height:21px;margin-top:8px}
.input{height:32px;background:#fff;border:1px solid #ddd;margin-top:10px;font-size:10px;color:#999;line-height:30px;padding:0 12px;border-radius:2px}
.wizards .input{width:185px}
.wizards .input.tall{height:58px}
.send-btn{display:block;margin:12px 0 0 95px;width:90px;height:30px;background:var(--blue-deep);color:#fff;font-size:11px;font-weight:700;text-align:center;line-height:30px;border-radius:2px}
.alert{background:var(--side-grey);height:294px;padding:18px 22px 0 23px}
.alert h3{color:var(--blue-deep)}
.alert p{font-size:11px;line-height:21px;color:#666;margin-top:8px}
.alert .input{width:185px;margin-top:12px}
.alert .select{position:relative}
.alert .select::after{content:"";position:absolute;right:12px;top:13px;border:4px solid transparent;border-top-color:#555}
.subscribe-btn{display:block;margin:12px 0 0 86px;width:99px;height:32px;background:var(--blue-deep);color:#fff;font-size:11px;font-weight:700;text-align:center;line-height:32px;border-radius:2px}
.about{background:var(--side-grey);height:299px;margin-top:14px;padding:24px 22px 0 25px}
.about h3{color:var(--blue-deep)}
.about p{font-size:11px;line-height:21px;color:#666;margin-top:10px}
.about a{display:block;font-size:11px;color:var(--blue-deep);margin-top:10px;font-weight:600}

/* main column */
.main{position:absolute;left:100px;top:0;width:743px}
.section-head{position:absolute;left:2px;width:741px;display:flex;justify-content:space-between;align-items:center}
.section-head h2{font-size:15px;font-weight:700;text-transform:uppercase;color:#222}
.section-head h2 small{font-size:12px;font-weight:400}
.section-head .arrows{font-size:14px;color:#666;letter-spacing:6px}
.panel{position:absolute;left:0;width:743px;background:#fff;box-shadow:0 1px 2px rgba(0,0,0,.06)}
.card-grid{display:grid;grid-template-columns:repeat(4,163px);column-gap:19.5px;row-gap:18px;padding:17px 18px 0}
.card .thumb{height:145px;position:relative}
.card .city{position:absolute;left:0;bottom:0;width:100%;height:28px;background:rgba(0,0,0,.55);color:#fff;font-size:12px;line-height:28px;padding-left:10px}
.card h4{font-size:12px;font-weight:600;color:var(--title-orange);margin-top:16px}
.card .type{font-size:11px;color:#666;margin-top:4px}
.card .view{display:block;height:38px;margin-top:12px;background:var(--btn);border:1px solid var(--btn-border);text-align:center;line-height:36px;font-size:12px;color:#888}
.card .view.active{background:var(--orange);border-color:var(--orange-deep);color:#fff}
.t1{background:linear-gradient(#9fbcd6,#4d5a66)}
.t2{background:linear-gradient(#1d2b46,#6a5030)}
.t3{background:linear-gradient(#8fb0cf,#5d6a70)}
.t4{background:linear-gradient(#b9cde0,#7c8a90)}
.t5{background:linear-gradient(#1a1a24,#7a3a20)}
.t6{background:linear-gradient(#20243a,#a0521e)}
.t7{background:linear-gradient(#5a7ca8,#8a6a3a)}
.t8{background:linear-gradient(#2a3d5a,#3e6f6a)}
.t9{background:linear-gradient(#a8c3df,#8a6e50)}
.t10{background:linear-gradient(#2a2f4a,#5a6078)}
.t11{background:linear-gradient(#2b3d6a,#3a3a40)}
.t12{background:linear-gradient(#6e9ccd,#8d5a4a)}
.t13{background:linear-gradient(#2b5a9a,#6b8fb8)}
.t14{background:linear-gradient(#c7d7e7,#9aa8b6)}
.t15{background:linear-gradient(#1a2b6a,#5a4a7a)}
.t16{background:linear-gradient(#4d6fa8,#8aa0c0)}

.project{display:flex;padding:16px 18px}
.project .thumb{width:292px;flex-shrink:0;height:195px;background:linear-gradient(#c7d8e4 0%,#9fb3c0 45%,#6d8a6a 100%)}
.project dl{margin-left:34px;margin-top:6px;display:grid;grid-template-columns:90px 1fr;row-gap:10px;font-size:13px;align-content:start}
.project dt{color:var(--title-orange);position:relative;padding-right:22px;line-height:20px}
.project dt::after{content:":";position:absolute;right:12px;bottom:0}
.project dd{color:#666;font-size:12px;line-height:24px}
.project dd.name{color:var(--title-orange);font-size:15px;line-height:20px}
.project dd a{color:var(--title-orange);font-weight:600}

/* footer */
.site-footer{position:absolute;left:0;top:2066px;width:1200px;height:269px;background:var(--footer)}
.footer-cols{position:absolute;left:100px;top:32px;display:flex}
.footer-col h3{color:#fff;font-size:12px;font-weight:700;text-transform:uppercase}
.footer-col p,.footer-col li{color:var(--footer-text);font-size:10px;line-height:20px}
.footer-col p{margin-top:12px}
.editor{width:282px}
.editor p{width:215px}
.links{width:276px}
.links ul{list-style:none;margin-top:12px;display:grid;grid-template-columns:106px 1fr;row-gap:4px}
.links li::before{content:"›";margin-right:5px;color:#aaa}
.contact{width:205px}
.contact .ic{display:inline-block;width:9px;height:9px;background:#ccc;border-radius:2px;margin-right:6px;vertical-align:-1px}
.follow{width:220px}
.social{margin-top:12px;display:grid;grid-template-columns:120px 1fr;row-gap:12px}
.social span{color:var(--footer-text);font-size:10px;display:flex;align-items:center;gap:6px}
.social i{width:20px;height:20px;border:1px solid #999;display:inline-block}
.footer-brand{margin-top:22px;display:flex;align-items:center;gap:6px}
.footer-brand .dot{width:22px;height:22px;border-radius:50%;background:#fff}
.footer-brand .name{color:#fff;font-size:20px;font-weight:700}
.copyright{position:absolute;left:0;bottom:0;width:100%;height:48px;background:var(--footer-bottom);color:var(--footer-text);font-size:10px;text-align:center;line-height:48px}
</style>
</head>
<body>

<nav class="city-bar">
  <a>Bangalore</a><a>Chennai</a><a>Greater Noida</a><a>Gurgaon</a><a>Hyderabad</a><a>Jaipur</a><a>Khanna</a><a>Kolkatta</a><a>Mumbai</a><a>Noida</a><a>Pune</a><a>Surat</a>
</nav>

<header class="site-header">
  <div class="brand"><span class="brand-dot"></span><span class="brand-name">lotstallmart</span></div>
  <div class="brand-tag">INDIA'S LEADING PORTAL FOR RETAIL SPACE</div>
  <div class="header-nav">
    <div class="item"><div class="label">Advertise with us</div><div class="sub">Standard listing - FREE »</div></div>
    <div class="item"><div class="label">Mart Wizards</div><div class="sub">Shop Search Services »</div></div>
    <div class="item"><div class="label">Listing Alert</div><div class="sub">Shop Search Services »</div></div>
  </div>
  <div class="login-btns">
    <a class="advertiser">Advertiser Login »</a>
    <a class="register">New Register Login »</a>
  </div>
</header>

<section class="hero">
  <form class="search-panel">
    <h2>SELECT RETAIL FORMAT:</h2>
    <div class="sub-title">Meaning of Retail Format</div>
    <div class="format-box">
      <label><span class="check"></span>Retail Malls</label>
      <label><span class="check"></span>Shopping Complex</label>
      <label><span class="check"></span>High Street Shops</label>
      <label><span class="check"></span>Retail Warehouses</label>
    </div>
    <div class="field">Sale Or Rent Or Both:</div>
    <div class="field">Select City:</div>
    <div class="field">Select Locality/Micro-Market.</div>
    <div class="field">Enter Keywords:</div>
    <span class="search-btn"><svg width="12" height="12" viewBox="0 0 12 12"><circle cx="5" cy="5" r="3.6" fill="none" stroke="#fff" stroke-width="1.8"/><line x1="7.6" y1="7.6" x2="11" y2="11" stroke="#fff" stroke-width="2"/></svg>Search Now</span>
  </form>
  <div class="hero-photo" role="img" aria-label="Banner photo of a family walking with shopping bags through a lit evening shopping arcade">
    <div class="hero-arrows"><span>‹</span><span>›</span></div>
  </div>
</section>

<aside class="sidebar">
  <div class="cat-tile"><h3>Retail Malls</h3><p>Centrally air-conditioned<span class="ring"></span></p></div>
  <div class="cat-tile"><h3>Shopping Complex</h3><p>Non air-conditioned building<span class="ring"></span></p></div>
  <div class="cat-tile"><h3>High Street Shops</h3><p>Road facing retail<span class="ring"></span></p></div>
  <div class="cat-tile"><h3>Retail Warehouses</h3><p>Back-end ratail storage<span class="ring"></span></p></div>
  <div class="wizards">
    <h3>Mart Wizards</h3>
    <p>Post your Retail Space requirement with us and our experts shall get back with suitable options and even help you in your transaction. This is a Free Service!</p>
    <div class="input">Enter your email address :</div>
    <div class="input">Mobile :</div>
    <div class="input tall">Discription of requirement :</div>
    <span class="send-btn">SEND</span>
  </div>
  <div class="alert">
    <h3>Listing Alert</h3>
    <p>Suscribe for Fortnightly Email update on New Listings @ lotstallmart</p>
    <div class="input">Enter your email address :</div>
    <div class="input select">Select option :</div>
    <div class="input select">select cities of interest</div>
    <span class="subscribe-btn">SUBSCRIBE</span>
  </div>
  <div class="about">
    <h3>www.lotstallmart.com</h3>
    <p>Lotstallmart.com - About Us Lotstallmart.com is a Specialised Web based platform for Retail Space, featuring properties across India under various formats such as Retail Malls.</p>
    <p>Retail Space, featuring properties across India under various...</p>
    <a>[ Read More + ]</a>
  </div>
</aside>

<main class="main">
  <div class="section-head" style="top:591px"><h2>Featured Retail Projects <small>ACROSS INDIA</small></h2><span class="arrows">‹›</span></div>
  <section class="panel" style="top:630px;height:546px">
    <div class="card-grid">
      <article class="card"><div class="thumb t1" role="img" aria-label="Retail building photo"><span class="city">Surat</span></div><h4>Corven Ashby</h4><div class="type">Shopping Complex</div><a class="view active">View the listing</a></article>
      <article class="card"><div class="thumb t2" role="img" aria-label="Shopping complex at night photo"><span class="city">Fairdabad</span></div><h4>Corven Ashby</h4><div class="type">Shopping Complex</div><a class="view">View the listing</a></article>
      <article class="card"><div class="thumb t3" role="img" aria-label="Glass-fronted mall photo"><span class="city">Gurgaon</span></div><h4>Corven Ashby</h4><div class="type">Shopping Complex</div><a class="view">View the listing</a></article>
      <article class="card"><div class="thumb t4" role="img" aria-label="Tower development photo"><span class="city">Surat</span></div><h4>Corven Ashby</h4><div class="type">Shopping Complex</div><a class="view">View the listing</a></article>
      <article class="card"><div class="thumb t5" role="img" aria-label="Lit mall facade photo"><span class="city">Surat</span></div><h4>Corven Ashby</h4><div class="type">Shopping Complex</div><a class="view">View the listing</a></article>
      <article class="card"><div class="thumb t6" role="img" aria-label="Mall entrance at night photo"><span class="city">Fairdabad</span></div><h4>Corven Ashby</h4><div class="type">Shopping Complex</div><a class="view">View the listing</a></article>
      <article class="card"><div class="thumb t7" role="img" aria-label="Mall exterior at dusk photo"><span class="city">Gurgaon</span></div><h4>Corven Ashby</h4><div class="type">Shopping Complex</div><a class="view">View the listing</a></article>
      <article class="card"><div class="thumb t8" role="img" aria-label="Modern mall building photo"><span class="city">Surat</span></div><h4>Corven Ashby</h4><div class="type">Shopping Complex</div><a class="view">View the listing</a></article>
    </div>
  </section>

  <section class="panel project" style="top:1197px;height:227px">
    <div class="thumb" role="img" aria-label="Aerial render of a retail project with towers and greenery"></div>
    <dl>
      <dt>Name</dt><dd class="name">Qelvo Centrix</dd>
      <dt>City</dt><dd>Haryana</dd>
      <dt>Locality</dt><dd>Gurgaon, zip code : 122015</dd>
      <dt>Retail<br>Format</dt><dd>It is surrounded by already populated and upmarket areas like sectors 47, 49, 50, 56 and 57 and upcoming affluent sectors 65, 66, 67, 68 with projected population... <a>[ Read More ]</a></dd>
    </dl>
  </section>

  <div class="section-head" style="top:1449px"><h2>Featured New Launches <small>ACROSS INDIA</small></h2><span class="arrows">‹›</span></div>
  <section class="panel" style="top:1489px;height:543px">
    <div class="card-grid">
      <article class="card"><div class="thumb t9" role="img" aria-label="Retail building photo"><span class="city">Surat</span></div><h4>Corven Ashby</h4><div class="type">Shopping Complex</div><a class="view">View the listing</a></article>
      <article class="card"><div class="thumb t10" role="img" aria-label="Curved glass mall photo"><span class="city">Fairdabad</span></div><h4>Corven Ashby</h4><div class="type">Shopping Complex</div><a class="view">View the listing</a></article>
      <article class="card"><div class="thumb t11" role="img" aria-label="Dark glass complex photo"><span class="city">Gurgaon</span></div><h4>Corven Ashby</h4><div class="type">Shopping Complex</div><a class="view">View the listing</a></article>
      <article class="card"><div class="thumb t12" role="img" aria-label="Mall with red signage photo"><span class="city">Surat</span></div><h4>Corven Ashby</h4><div class="type">Shopping Complex</div><a class="view">View the listing</a></article>
      <article class="card"><div class="thumb t13" role="img" aria-label="Blue glass office block photo"><span class="city">Surat</span></div><h4>Corven Ashby</h4><div class="type">Shopping Complex</div><a class="view">View the listing</a></article>
      <article class="card"><div class="thumb t14" role="img" aria-label="Tall glass towers photo"><span class="city">Fairdabad</span></div><h4>Corven Ashby</h4><div class="type">Shopping Complex</div><a class="view">View the listing</a></article>
      <article class="card"><div class="thumb t15" role="img" aria-label="Mall at night photo"><span class="city">Gurgaon</span></div><h4>Corven Ashby</h4><div class="type">Shopping Complex</div><a class="view">View the listing</a></article>
      <article class="card"><div class="thumb t16" role="img" aria-label="Glass canopy mall photo"><span class="city">Surat</span></div><h4>Corven Ashby</h4><div class="type">Shopping Complex</div><a class="view">View the listing</a></article>
    </div>
  </section>
</main>

<footer class="site-footer">
  <div class="footer-cols">
    <div class="footer-col editor">
      <h3>Editor's Choice</h3>
      <p>A "Select" Listing of Retail Properties Handpicked by our Editors based on their own positive evaluation on parameters &amp; attributes such as Design Concept, Location, Developer, Success Potential. So Read On to Check Out for yourself ..</p>
    </div>
    <div class="footer-col links">
      <h3>About Vistral Bazaar</h3>
      <ul>
        <li>About Us</li><li>Retail Malls</li>
        <li>Privacy Policy</li><li>Shopping Complex</li>
        <li>Terms of Use</li><li>High Street Shops</li>
        <li>Contact Us</li><li>Retail Warehouses</li>
        <li>Site Map</li>
      </ul>
    </div>
    <div class="footer-col contact">
      <h3>Contact</h3>
      <p>Vistral Bazaar<br>Unit 212, 3rd Floor,<br>Sector-x, Gurgaon - 122015<br><span class="ic"></span>Phone : 000-000-0000<br><span class="ic"></span>Fax : 000 - 000 - 0000</p>
    </div>
    <div class="footer-col follow">
      <h3>Follow Us</h3>
      <div class="social">
        <span><i></i>: Friendlane</span><span><i></i>: Chirpnet</span>
        <span><i></i>: Workgrid</span><span><i></i>: Circlespace</span>
      </div>
      <div class="footer-brand"><span class="dot"></span><span class="name">lotstallmart</span></div>
    </div>
  </div>
  <div class="copyright">Copyright © 2015. Vistral Bazaar.com. All rights reserved.</div>
</footer>

</body>
</html>
```